Business Cards for a law firm

Business cards for our law firm. Use our silhoette logo and OAK PARTNERS - check our website (www.oakpartners.example)

Contact Information for Business Card

our silhouette logo, OAK PARTNERS, 800-555-0147, Dorian Pemberton, dorian@oakpartners.example

Requirements
Must have
• our silhouette logo, OAK PARTNERS, 800-555-0147, Dorian Pemberton, dorian@oakpartners.example

```html
<!DOCTYPE html>
<html lang="en">
<head>
<meta charset="utf-8">
<title>Oak Partners – Business Cards</title>
<link rel="stylesheet" href="https://fonts.googleapis.com/css2?family=Montserrat:wght@400;500;700&display=swap">
<style>
  :root {
    --navy: #22306b;
    --grey: #9a9a9c;
    --paper: #ffffff;
    --backdrop: #e9e9ec;
    --ink: #1c1c22;
  }
  * { box-sizing: border-box; margin: 0; padding: 0; }
  html, body {
    width: 1200px; height: 900px; overflow: hidden;
    background: var(--backdrop);
    font-family: "Montserrat", sans-serif;
  }
  .canvas {
    position: relative; width: 1200px; height: 900px;
  }
  .card {
    position: absolute; left: 250px;
    width: 700px; height: 400px;
    background: var(--paper);
    border-radius: 28px;
    overflow: hidden;
    box-shadow: 0 10px 30px rgba(0,0,0,0.18);
  }
  .card--front { top: 40px; }
  .card--back { top: 465px; }

  .brand {
    position: absolute;
    display: flex; align-items: center; gap: 18px;
    color: var(--navy);
    font-weight: 400;
    letter-spacing: 0.08em;
    white-space: nowrap;
  }
  .brand__mark {
    width: 22px; height: 22px; background: var(--navy);
  }
  .card--front .brand { left: 110px; top: 165px; font-size: 50px; }
  .card--back .brand { left: 80px; top: 80px; font-size: 50px; }

  .holder {
    position: absolute; right: 420px; top: 232px;
    text-align: right; color: var(--navy);
  }
  .holder__name { font-weight: 700; font-size: 27px; line-height: 1.1; }
  .holder__title { font-weight: 400; font-size: 17px; color: var(--ink); margin-top: 2px; }

  .divider {
    position: absolute; left: 305px; top: 240px;
    width: 2px; height: 62px; background: var(--navy);
  }

  .contacts {
    position: absolute; left: 328px; top: 236px;
    list-style: none; color: var(--ink);
    font-weight: 500; font-size: 17px;
  }
  .contacts li { display: flex; align-items: center; gap: 10px; height: 24px; }
  .contacts svg { width: 14px; height: 14px; fill: var(--navy); flex: none; }

  .swoosh { position: absolute; left: 0; bottom: 0; width: 700px; height: 400px; }
</style>
</head>
<body>
<main class="canvas">
  <section class="card card--front" aria-label="Card front">
    <div class="brand"><span class="brand__mark"></span><span class="brand__name">OAK PARTNERS</span></div>
  </section>

  <section class="card card--back" aria-label="Card back">
    <svg class="swoosh" viewBox="0 0 700 400" aria-hidden="true">
      <path d="M170,330 C380,345 560,372 650,400 L575,400 C450,365 320,345 170,330 Z" fill="var(--grey)"/>
      <path d="M0,305 C180,325 400,345 575,400 L0,400 Z" fill="var(--navy)"/>
    </svg>

    <div class="brand"><span class="brand__mark"></span><span class="brand__name">OAK PARTNERS</span></div>

    <div class="holder">
      <p class="holder__name">Dorian Pemberton</p>
      <p class="holder__title">Attorney at Law</p>
    </div>

    <div class="divider"></div>

    <ul class="contacts">
      <li>
        <svg viewBox="0 0 16 16"><path d="M3 1h3l1.5 4-2 1.3a9 9 0 0 0 4.2 4.2L11 8.5l4 1.5v3a2 2 0 0 1-2 2A13 13 0 0 1 1 3a2 2 0 0 1 2-2z"/></svg>
        <span>800-555-0147</span>
      </li>
      <li>
        <svg viewBox="0 0 16 16"><path d="M1 3h14v1.5L8 9 1 4.5z M1 6.3 8 10.8l7-4.5V13H1z"/></svg>
        <span>dorian@oakpartners.example</span>
      </li>
      <li>
        <svg viewBox="0 0 16 16"><circle cx="8" cy="8" r="6.5" fill="none" stroke="var(--navy)" stroke-width="1.6"/><path d="M1.5 8h13M8 1.5c-3 3.5-3 9.5 0 13M8 1.5c3 3.5 3 9.5 0 13" fill="none" stroke="var(--navy)" stroke-width="1.2"/></svg>
        <span>www.oakpartners.example</span>
      </li>
    </ul>
  </section>
</main>
</body>
</html>
```